Ferrow Sky Operations E-mail Signature

Need to create an email signature for Ferrow Sky Operations. Signature should include the Ferrow logo and the associated TLVQ member logo

```html
<!DOCTYPE html>
<html lang="en">
<head>
<meta charset="utf-8">
<title>Ferrow Sky Operations – E-mail Signature</title>
<link rel="stylesheet" href="https://fonts.googleapis.com/css2?family=Montserrat:wght@400;500;600&display=swap">
<style>
  :root {
    --page: #e4e5e7;
    --card: #ffffff;
    --brand-blue: #0b63b3;
    --ink: #111111;
    --band-dark: #000000;
    --white: #ffffff;
  }
  * { box-sizing: border-box; margin: 0; padding: 0; }
  html, body {
    width: 1069px; height: 1200px; overflow: hidden;
    background: var(--page);
    font-family: "Montserrat", Arial, sans-serif;
    color: var(--ink);
  }
  .signature {
    position: absolute; left: 88px;
    width: 919px; height: 277px;
    background: var(--card);
    border-radius: 20px;
    overflow: hidden;
  }
  .signature--one { top: 84px; }
  .signature--two { top: 448px; }
  .signature--three { top: 827px; }

  .brand {
    position: absolute; left: 80px; top: 118px;
    color: var(--brand-blue); font-weight: 600;
    line-height: 1;
  }
  .brand__name { font-size: 30px; letter-spacing: 1px; display: block; }
  .brand__sub { font-size: 11.5px; letter-spacing: 1.4px; display: block; margin-top: 4px; }

  .divider {
    position: absolute; left: 279px; top: 56px;
    width: 1px; height: 137px; background: var(--ink);
  }

  .person { position: absolute; left: 335px; top: 70px; }
  .person__name {
    font-size: 26px; font-weight: 600; letter-spacing: 0.8px; line-height: 1;
  }
  .person__role { font-size: 17px; font-weight: 400; margin-top: 9px; letter-spacing: 0.3px; }
  .signature--three .person__name { color: var(--brand-blue); }

  .address {
    position: absolute; left: 341px; top: 171px;
    font-size: 9px; font-weight: 400;
  }
  .address b { font-weight: 600; }

  .social { position: absolute; left: 709px; top: 48px; display: flex; gap: 10px; }
  .social__dot {
    width: 33px; height: 33px; border-radius: 50%;
    background: var(--brand-blue);
  }

  .membership { position: absolute; left: 744px; top: 152px; }
  .membership__label {
    position: absolute; left: 37px; top: 0; font-size: 7px; font-weight: 500; white-space: nowrap;
  }
  .membership__mark {
    position: absolute; left: 0; top: 10px; width: 30px; height: 19px;
    border-radius: 50%; background: var(--brand-blue);
  }
  .membership__name {
    position: absolute; left: 37px; top: 9px; font-size: 19px; font-weight: 600;
    letter-spacing: 4px; line-height: 1;
  }

  .contact-band {
    position: absolute; left: 272px; top: 206px;
    width: 647px; height: 71px;
    background: var(--brand-blue);
    border-top-left-radius: 72px;
    color: var(--white);
    font-size: 12.5px; font-weight: 500;
  }
  .signature--three .contact-band { background: var(--band-dark); }
  .contact {
    position: absolute; top: 0; height: 71px;
    display: flex; align-items: center; gap: 6px; white-space: nowrap;
  }
  .contact__icon { width: 19px; height: 19px; flex: none; }
</style>
</head>
<body>

<section class="signature signature--one">
  <div class="brand"><span class="brand__name">FERROW</span><span class="brand__sub">SKY OPERATIONS</span></div>
  <div class="divider"></div>
  <div class="person">
    <h1 class="person__name">ADRIAN LOWELL</h1>
    <p class="person__role">Marketing Expert</p>
  </div>
  <p class="address"><b>address :</b> Your Street Address Her, New Your Sity Aip - 000</p>
  <div class="social" role="img" aria-label="Social profile links">
    <span class="social__dot"></span><span class="social__dot"></span><span class="social__dot"></span><span class="social__dot"></span>
  </div>
  <div class="membership">
    <span class="membership__label">member of</span>
    <span class="membership__mark"></span>
    <span class="membership__name">TLVQ</span>
  </div>
  <div class="contact-band">
    <span class="contact" style="left:70px">p : 00 123 456 7890</span>
    <span class="contact" style="left:221px">e : username@mail.com</span>
    <span class="contact" style="left:413px">w : www.websitename.com</span>
  </div>
</section>

<section class="signature signature--two">
  <div class="brand"><span class="brand__name">FERROW</span><span class="brand__sub">SKY OPERATIONS</span></div>
  <div class="divider"></div>
  <div class="person">
    <h1 class="person__name">ADRIAN LOWELL</h1>
    <p class="person__role">Marketing Expert</p>
  </div>
  <p class="address"><b>address :</b> Your Street Address Her, New Your Sity Aip - 000</p>
  <div class="social" role="img" aria-label="Social profile links">
    <span class="social__dot"></span><span class="social__dot"></span><span class="social__dot"></span><span class="social__dot"></span>
  </div>
  <div class="membership">
    <span class="membership__label">member of</span>
    <span class="membership__mark"></span>
    <span class="membership__name">TLVQ</span>
  </div>
  <div class="contact-band">
    <span class="contact" style="left:70px">
      <svg class="contact__icon" viewBox="0 0 20 20"><circle cx="10" cy="10" r="10" fill="#fff"/><path d="M6.5 5.5l2 .2.8 2.3-1.2 1a6 6 0 0 0 3 3l1-1.2 2.3.8.2 2c-.4.8-1.3 1.1-2 1A8.5 8.5 0 0 1 5.5 7.5c-.1-.8.2-1.6 1-2z" fill="var(--brand-blue)"/></svg>
      00 123 456 7890</span>
    <span class="contact" style="left:222px">
      <svg class="contact__icon" viewBox="0 0 20 20"><circle cx="10" cy="10" r="10" fill="#fff"/><rect x="5" y="6.5" width="10" height="7" rx="1" fill="var(--brand-blue)"/><path d="M5.5 7l4.5 3.5L14.5 7" fill="none" stroke="#fff" stroke-width="1"/></svg>
      username@mail.com</span>
    <span class="contact" style="left:418px">
      <svg class="contact__icon" viewBox="0 0 20 20"><circle cx="10" cy="10" r="10" fill="#fff"/><g fill="none" stroke="var(--brand-blue)" stroke-width="1.1"><circle cx="10" cy="10" r="5"/><ellipse cx="10" cy="10" rx="2.2" ry="5"/><path d="M5 10h10"/></g></svg>
      www.websitename.com</span>
  </div>
</section>

<section class="signature signature--three">
  <div class="brand"><span class="brand__name">FERROW</span><span class="brand__sub">SKY OPERATIONS</span></div>
  <div class="divider"></div>
  <div class="person">
    <h1 class="person__name">ADRIAN LOWELL</h1>
    <p class="person__role">Marketing Expert</p>
  </div>
  <p class="address"><b>address :</b> Your Street Address Her, New Your Sity Aip - 000</p>
  <div class="social" role="img" aria-label="Social profile links">
    <span class="social__dot"></span><span class="social__dot"></span><span class="social__dot"></span><span class="social__dot"></span>
  </div>
  <div class="membership">
    <span class="membership__label">member of</span>
    <span class="membership__mark"></span>
    <span class="membership__name">TLVQ</span>
  </div>
  <div class="contact-band">
    <span class="contact" style="left:70px">
      <svg class="contact__icon" viewBox="0 0 20 20"><circle cx="10" cy="10" r="10" fill="#fff"/><path d="M6.5 5.5l2 .2.8 2.3-1.2 1a6 6 0 0 0 3 3l1-1.2 2.3.8.2 2c-.4.8-1.3 1.1-2 1A8.5 8.5 0 0 1 5.5 7.5c-.1-.8.2-1.6 1-2z" fill="#000"/></svg>
      00 123 456 7890</span>
    <span class="contact" style="left:222px">
      <svg class="contact__icon" viewBox="0 0 20 20"><circle cx="10" cy="10" r="10" fill="#fff"/><rect x="5" y="6.5" width="10" height="7" rx="1" fill="#000"/><path d="M5.5 7l4.5 3.5L14.5 7" fill="none" stroke="#fff" stroke-width="1"/></svg>
      username@mail.com</span>
    <span class="contact" style="left:418px">
      <svg class="contact__icon" viewBox="0 0 20 20"><circle cx="10" cy="10" r="10" fill="#fff"/><g fill="none" stroke="#000" stroke-width="1.1"><circle cx="10" cy="10" r="5"/><ellipse cx="10" cy="10" rx="2.2" ry="5"/><path d="M5 10h10"/></g></svg>
      www.websitename.com</span>
  </div>
</section>

</body>
</html>
```